Open Harbor book needs a cover design

I need a front and back cover design that demonstrates a strong sense of possibility that trust can be repaired even if things look bleak. Repairing trust is difficult, but this book is full of wisdom, proven strategies, and doctoral research to help people strengthen relationships and improve trust. It can help any group: business, nonprofit, education, service. Showing diversity of groups and people is very important. For the cover title, there should be a play on words: "Open Harbor: Is it? Within Reach" should have the words "is it?" crossed out and the words "It IS! should be replaced there in a striking way. Perhaps in red ink. For publishing purposes, book will be titled Open Harbor: It IS Within Reach! Please see the attachment for an example. The book layout is approximately 260 pages.

A business self-help book, but the target is any person in a group that feels they have lost trust in each other. It can be just a normal person struggling in a volunteer group they are a part of, or a supervisor whose group is not working well together. It can be a leader who just wants their group to be stronger.

Business Management

• Allise - I believe is being used on the interior of the book for the title page and headings

• Show hope and possibility in the midst of difficulty. Must have a play on the words in the title "Open Harbor: Is it? Within Reach" with crossing out "is it?" with "It IS!" (see attached example) Must include the author's name: Marla Quentin, PhD Must include a smaller tagline: "Practical Steps to Move Teams Forward Again"
• Showing diverse people, or hands. Diverse kinds of groups - not just business. A colorful cover. Maybe show the complexity of trust when it is broken...broken pieces of trust that are then picked up and put together when people work together. Could show people (or images of hands) or other ways to show that it's a choice and it is possible to repair broken trust. I'd also like to convey a sense of a group - not just random people. That they have something at stake to work on repairing trust together and this book can help them.
• If images of people are used, just showing one gender or race is not okay. Nor just binary choices: like an image containing one man and one woman, or one white person and one person of color - otherwise it seems that the book on Open Harbor is about race or gender relations.

```html
<!DOCTYPE html>
<html lang="en">
<head>
<meta charset="utf-8">
<title>Open Harbor: It is Within Reach! — Marla Quentin, PhD</title>
<link rel="stylesheet" href="https://fonts.googleapis.com/css2?family=Fresca&display=swap">
<style>
  :root {
    --paper: #ffffff;
    --ink: #262422;
    --strike: #e0252a;
    --leaf: #6f9a2e;
    --bark-dark: #2a2420;
    --bark-mid: #5a4a3e;
    --sprout: #6fae3a;
  }
  * { margin: 0; padding: 0; box-sizing: border-box; }
  html, body {
    width: 800px;
    height: 1200px;
    overflow: hidden;
    background: var(--paper);
  }
  .cover {
    position: relative;
    width: 800px;
    height: 1200px;
    background: var(--paper);
    font-family: "Fresca", "Trebuchet MS", sans-serif;
    color: var(--ink);
    text-align: center;
  }
  .title {
    position: absolute;
    top: 78px;
    left: 0;
    width: 100%;
    font-weight: 400;
  }
  .title-main,
  .title-answer {
    display: block;
    font-size: 104px;
    line-height: 1;
    letter-spacing: 0.5px;
  }
  .title-question {
    display: block;
    font-size: 74px;
    line-height: 1;
    margin-top: 6px;
    margin-bottom: 12px;
  }
  .title-question .struck {
    position: relative;
    display: inline-block;
  }
  .title-question .struck::after {
    content: "";
    position: absolute;
    left: -6px;
    right: -10px;
    top: 44%;
    height: 6px;
    background: var(--strike);
    border-radius: 3px;
    transform: rotate(-4deg);
  }
  .title-answer { font-size: 96px; }

  .cover-photo {
    position: absolute;
    left: 168px;
    top: 408px;
    width: 464px;
    height: 480px;
    border-radius: 50%;
    background:
      radial-gradient(ellipse 22% 20% at 50% 42%, var(--sprout) 0%, rgba(111,174,58,0.6) 45%, rgba(111,174,58,0) 100%),
      radial-gradient(ellipse 50% 50% at 50% 50%, var(--bark-mid) 0%, var(--bark-dark) 55%, rgba(42,36,32,0.6) 78%, rgba(255,255,255,0) 100%);
  }

  .tagline {
    position: absolute;
    top: 906px;
    left: 0;
    width: 100%;
    font-size: 48px;
    line-height: 60px;
    color: var(--leaf);
    font-weight: 400;
  }
  .author {
    position: absolute;
    top: 1090px;
    left: 0;
    width: 100%;
    font-size: 44px;
    line-height: 1;
    color: var(--ink);
  }
</style>
</head>
<body>
  <main class="cover">
    <h1 class="title">
      <span class="title-main">Open Harbor:</span>
      <span class="title-question"><span class="struck">Is it?</span></span>
      <span class="title-answer">It is Within Reach!</span>
    </h1>

    <div class="cover-photo" role="img" aria-label="Photograph of a hollow, weathered tree stump with a small green sapling growing out of its centre, fading softly into white at the edges"></div>

    <p class="tagline">Practical Steps to Move<br>Teams Forward Again</p>

    <p class="author">Marla Quentin, PhD</p>
  </main>
</body>
</html>
```